Internal Company (Private/Invite only) blog

I need a template for an internal company blog.
We are an FMCG organisation operating in Saudi Arabia. We have large number of partners working with us across multiple countries.
This blog is primarily designed to inform our shareholders of progress/updates, new information etc.
It will be published/updated weekly

Target Market(s)

audience is company stakeholders only

Industry/Entity Type

It Company

Requirements
Must have
• - Core feature must be that this can be secure/private as we wish to submit information that is only for a registered list of readers.

- ability to update content with images and content
Nice to have
• Some elements we have thought of
- Contact details
- Personnel Bio's
- Weekly product review
- Status on activities
- Case studies
- Future discussion points
- Glossary of terms
- submit your question/idea

Also would like to have ability to have published posts sent to the readers either as a link or as an email with the new content in the message body of the email
Should not have
• No complicated interface.
Should be easy, clean and simple layout
No business type imagery such as pie charts, graphs etc

```html
<!DOCTYPE html>
<html lang="en">
<head>
<meta charset="utf-8">
<title>Stakeholder Blog</title>
<link rel="stylesheet" href="https://fonts.googleapis.com/css2?family=Arimo:wght@400;700&display=swap">
<style>
:root{
  --ink:#2b2b2b;
  --title:#1a1a1a;
  --link:#1a7fc9;
  --meta:#8a8a8a;
  --meta-link:#1d3f7a;
  --panel-top:#3d92e2;
  --panel-bottom:#0c5aa6;
  --panel-edge:#0a4f94;
  --white:#ffffff;
  --frame:#cfcfcf;
  --band:#d9ecfb;
}
*{box-sizing:border-box;margin:0;padding:0}
html,body{width:1200px;height:991px;overflow:hidden;background:var(--white)}
body{position:relative;font-family:"Arimo",Arial,sans-serif;color:var(--ink);font-size:12.5px;line-height:18px}
.abs{position:absolute}
.post-text p{margin-bottom:18px}
.photo-frame{border:1px solid var(--frame);padding:4px;background:var(--white)}
.photo-frame div{width:100%;height:100%}
.continue{color:var(--link);font-size:11.5px;text-decoration:underline}
.post-title{font-size:18px;line-height:22px;color:var(--title);font-weight:400}
.post-rule{border-top:2px dotted #b8b8b8}
.post-meta{font-size:10px;color:var(--meta)}
.post-meta a{color:var(--meta-link);font-weight:700;text-decoration:underline}
.share-row{display:flex;gap:4px;align-items:center}
.share-btn{height:19px;border:1px solid #c9c9c9;border-radius:3px;background:linear-gradient(#fff,#e8e8e8);font-size:10.5px;color:#555;padding:0 6px;line-height:17px;display:flex;align-items:center;gap:4px}
.share-btn i{width:11px;height:11px;border-radius:2px;display:inline-block}
.count{height:19px;border:1px solid #c9c9c9;font-size:10.5px;padding:0 6px;line-height:17px;color:#555}
.panel{background:linear-gradient(var(--panel-top),var(--panel-bottom));border:1px solid var(--panel-edge);border-radius:9px;color:var(--white);box-shadow:inset 0 0 0 1px rgba(255,255,255,.25)}
.panel h2{font-weight:400;font-size:19px;line-height:24px;margin:8px 12px 0;padding-bottom:8px;border-bottom:1px solid rgba(255,255,255,.3)}
.tag-cloud{padding:3px 14px 0 20px}
.tag-row{display:block;height:20px;line-height:20px;white-space:nowrap}
.tag-cloud a{color:var(--white);text-decoration:underline;font-size:10px;margin-right:5px}
.tag-cloud a.lg{font-size:13px}
.archive-list{list-style:none;padding:12px 0 0 12px}
.archive-list li{font-size:11px;line-height:20px}
.archive-list li::before{content:"»";margin-right:12px;font-weight:700}
.archive-list a{color:var(--white);text-decoration:underline}
.footer-band{background:linear-gradient(90deg,rgba(217,236,251,0),var(--band) 15%,var(--band) 85%,rgba(217,236,251,0));border-top:2px solid #9fb3c4}
.footer-nav{font-size:11px;color:#222}
.footer-nav span{margin:0 9px;color:#444}
.copyright{font-size:10.5px;color:#222}
.subscribe-title{font-size:14px;color:#111}
.subscribe-field{border:1px solid #9a9a9a;border-radius:4px;background:var(--white);font-size:11px;color:#a5a5a5;padding:2px 6px;line-height:18px;box-shadow:inset 1px 1px 2px rgba(0,0,0,.15)}
</style>
</head>
<body>

<!-- First post (continued) -->
<div class="abs post-text" style="left:97px;top:-4px;width:392px">
  <p>player inducted in the Hall of Fame, Neil Foster. Neil has included some excellent advice not only for players of the game, but writers as well.MLC is the creator, co-founder and host of the Maple Crew podcast, the edgiest show on Spellcraft Arena available online. Even with the success of this podcast, he has always wanted to do something that was safe for work and here it is, an interview with the only Canadian player inducted in the Hall of Fame, Neil Foster. Neil has included some excellent advice not only for players of the game, but writers as well.</p>
</div>
<div class="abs photo-frame" style="left:511px;top:-10px;width:273px;height:171px">
  <div role="img" aria-label="Stacked colourful letter blocks" style="background:linear-gradient(135deg,#f4f4f4,#e6e6e6 40%,#f2c23a 55%,#d9342f 80%,#f2f2f2)"></div>
</div>
<div class="abs post-text" style="left:97px;top:178px;width:690px">
  <p>MLC is the creator, co-founder and host of the Maple Crew podcast, the edgiest show on Spellcraft Arena available online. Even with the success of this podcast, he has always wanted to do something that was safe for work and here it is, an interview with the only Canadian player inducted in the Hall of Fame, Neil Foster. Neil has included some excellent advice not only for players of the game, but writers as well.</p>
  <p>MLC is the creator, co-founder and host of the Maple Crew podcast, the edgiest show on Spellcraft Arena available online. Even with the success of this podcast, he has always wanted to do something that was safe for work and here it is, an interview with the only Canadian player inducted in the Hall of Fame, Neil Foster.</p>
</div>
<a class="abs continue" style="left:99px;top:336px">Continue Reading</a>

<!-- Second post -->
<h1 class="abs post-title" style="left:97px;top:373px">Lorel IPsum Dolor sit amet</h1>
<div class="abs post-rule" style="left:97px;top:400px;width:686px"></div>
<div class="abs post-meta" style="left:97px;top:412px">Posted at 11:55 PM in <a>Mei Lin Cho</a>, <a>Podcasts</a> | <a>Permalink</a> | <a>Comments (0)</a></div>
<div class="abs share-row" style="left:97px;top:431px">
  <span class="share-btn"><i style="background:#7bbf4a"></i>Reblog (0)</span>
  <span class="share-btn"><i style="background:#8cc8ea"></i>Share This!</span>
  <span class="share-btn"><i style="background:#4a6aa8"></i>Like</span>
  <span class="count">2</span>
  <svg width="22" height="16" viewBox="0 0 22 16"><rect x="1" y="2" width="20" height="13" fill="#f4c430" stroke="#c99a10"/><path d="M1 2 L11 10 L21 2" fill="none" stroke="#c99a10"/></svg>
</div>
<div class="abs post-text" style="left:97px;top:469px;width:380px">
  <p>MLC is the creator, co-founder and host of the Maple Crew podcast, the edgiest show on Spellcraft Arena available online. Even with the success of this podcast, he has always wanted to do something that was safe for work and here it is, an interview with the only Canadian player inducted in the Hall of Fame, Neil Foster. Neil has included some excellent advice not only for players of the game, but writers as well.</p>
  <p>MLC is the creator, co-founder and host of the Maple Crew podcast, the edgiest show on Spellcraft Arena available online. Even with the success of this podcast, he has always wanted to do something that was safe for work and here it is, an interview with the only Canadian player inducted in the Hall of Fame, Neil Foster. Neil has included some excellent advice not only for players of the game, but writers as well.</p>
</div>
<div class="abs photo-frame" style="left:498px;top:449px;width:285px;height:312px">
  <div role="img" aria-label="Figure pushing a shopping cart among red discount cubes" style="background:radial-gradient(circle at 72% 45%,#9ad35a 0,#7cc23e 14%,rgba(255,255,255,0) 24%),radial-gradient(circle at 35% 55%,#e04a3c 0,#d7261b 20%,rgba(255,255,255,0) 45%),#f7f7f7"></div>
</div>
<a class="abs continue" style="left:100px;top:751px">Continue Reading</a>

<!-- Sidebar -->
<section class="abs panel" style="left:802px;top:12px;width:307px;height:187px">
  <h2>Categories</h2>
  <div class="tag-cloud">
    <span class="tag-row"><a>Ben Ashford</a> <a>Oliver Grant</a> <a>Harbor Town Games</a></span>
    <span class="tag-row"><a>Nadia Morrow</a> <a>Leo Pratt</a> <a>Deck Tech</a></span>
    <span class="tag-row"><a class="lg">Wes Carver EDH</a> <a>Extended</a> <a>Marcel Dupuis</a></span>
    <span class="tag-row"><a>Étienne Lavoie</a> <a>French General</a> <a>Tom Reid</a> <a>Interview</a></span>
    <span class="tag-row"><a class="lg">Samuel Whitfield</a> <a>Judge</a> <a>Ryan Holloway</a></span>
    <span class="tag-row"><a class="lg">Mei Lin Cho</a> <a>Hiro Sato</a> <a>Legacy</a></span>
  </div>
</section>
<section class="abs panel" style="left:802px;top:208px;width:307px;height:274px">
  <h2>Archieves</h2>
  <ul class="archive-list">
    <li><a>June 2011</a></li>
    <li><a>July 2011</a></li>
    <li><a>August 2011</a></li>
    <li><a>September 2011</a></li>
    <li><a>Decemeber 2011</a></li>
    <li><a>January 2012</a></li>
    <li><a>March 2012</a></li>
    <li><a>April 2012</a></li>
    <li><a>May 2012</a></li>
  </ul>
</section>

<!-- Footer -->
<footer>
  <div class="abs footer-band" style="left:90px;top:846px;width:1020px;height:70px"></div>
  <nav class="abs footer-nav" style="left:113px;top:873px">Home<span>|</span>Bios<span>|</span>Product Review<span>|</span>Activities<span>|</span>Case Studies<span>|</span>Discussion<span>|</span>Glossary<span>|</span>FAQ<span>|</span>Contact</nav>
  <div class="abs copyright" style="left:113px;top:892px">© 2012, All Rights Reserved</div>
  <div class="abs subscribe-title" style="left:829px;top:860px">Subscribe Newsletter</div>
  <div class="abs subscribe-field" style="left:828px;top:883px;width:250px;height:25px">Type your email id</div>
  <svg class="abs" style="left:1055px;top:886px" width="18" height="18" viewBox="0 0 18 18"><rect x="1" y="1" width="16" height="16" rx="2" fill="#fff" stroke="#333" stroke-width="1.5"/><path d="M4 9 L8 13 L15 4" fill="none" stroke="#111" stroke-width="2.2"/></svg>
</footer>

</body>
</html>
```